Tavenhurst Falcons FC Website

We are looking to develop a new website for Tavenhurst FC. Tavenhurst FC has now joined with Tavenhurst Falcons FC and we are looking at a website that can work for both clubs. Tavenhurst FC play in a local park football competition while tavenhurst Falcons are a Semi Professional team that plays in the Ostral Premier Series Competition. What we are after is two separate website off the one platform. I have attached both team logos for you to visualise. Also you can look at the existing tavenhurst website www.tavenhurstfc.net.au. We are looking for a huge improvement in the website and it will be imperative we have links to sponsors and the sponsors can get regular visuals. Weare looking to move this club forward and have a very professional website that can communicate clearly with the community.

Hi All,

Please remember that the website is to represent two clubs;
1. Tavenhurst Falcons FC (Competes in Semi Professional League)
2. Tavenhurst FC (Compete in KPWLT League which is a lower level)

Further to this the Tavenhurst Falcons FC page will require a player profile page which will show photos of each player and a little bio on each.

Thanks

Reason: Would like to spend more time review existing and new designs

```html
<!DOCTYPE html>
<html lang="en">
<head>
<meta charset="utf-8">
<title>Tavenhurst FC</title>
<link rel="stylesheet" href="https://fonts.googleapis.com/css2?family=Oswald:wght@300;400;500&family=Roboto+Condensed:wght@400;700&family=Open+Sans:wght@400;600&display=swap">
<style>
:root{
  --red:#c0131c;
  --red-dark:#9c0d14;
  --red-bright:#e3242b;
  --yellow:#f5c518;
  --yellow-dark:#d9a400;
  --ink:#222;
  --grey:#555;
  --light:#eef0f2;
  --footer:#242424;
  --footer-line:#3a3a3a;
  --white:#fff;
}
*{margin:0;padding:0;box-sizing:border-box}
html,body{width:1200px;height:2400px;overflow:hidden}
body{position:relative;font-family:"Open Sans",Arial,sans-serif;color:var(--ink);background:var(--white)}
.abs{position:absolute}

/* header */
.header{left:0;top:0;width:1200px;height:131px;z-index:3}
.header svg{position:absolute;left:0;top:0}
.brand{left:120px;top:28px;display:flex;align-items:center;gap:8px;font-family:"Roboto Condensed",sans-serif;font-weight:700;font-size:17px;color:var(--red)}
.brand-dot{width:34px;height:34px;border:3px solid var(--red);border-radius:50%}
.nav{left:285px;top:38px;display:flex;gap:0;font-family:"Roboto Condensed",sans-serif;font-size:14px;color:#333;list-style:none}
.nav li{margin-right:37px}
.nav li.active{color:var(--red)}

/* hero */
.hero{left:0;top:0;width:1200px;height:568px;background:radial-gradient(ellipse at 60% 40%,#3a3038 0%,#1c1418 55%,#0e0a0c 100%)}
.hero-player{left:96px;top:112px;width:464px;height:456px;background:linear-gradient(160deg,#6a1a1e 0%,#b3141c 45%,#5a0c10 100%);border-radius:40% 40% 0 0;opacity:.85}
.hero-mark{left:783px;top:196px;width:120px;text-align:center;color:var(--white);font-family:"Roboto Condensed",sans-serif;font-size:13px}
.hero-mark span{display:block;width:56px;height:56px;margin:0 auto 6px;border:3px solid var(--white);border-radius:50%}
.hero-title{left:600px;top:288px;width:486px;text-align:center;font-family:"Oswald",sans-serif;font-weight:300;font-size:60px;letter-spacing:3px;color:var(--white);line-height:1}
.hero-text{left:640px;top:374px;width:406px;text-align:center;font-size:15px;line-height:22px;color:#e6e0e0}
.btn-red{left:773px;top:459px;width:160px;height:37px;border-radius:19px;background:var(--red);border:2px solid var(--white);color:var(--white);font-size:13px;line-height:33px;text-align:center}
.arrow-left{left:0;top:322px;width:56px;height:44px;border-radius:0 22px 22px 0;border:2px solid var(--white);background:#1a1a1a}
.arrow-right{left:1128px;top:325px;width:72px;height:40px;border-radius:20px 0 0 20px;background:var(--red)}
.arrow-left svg,.arrow-right svg{position:absolute;top:50%;transform:translateY(-50%)}

/* welcome */
.welcome{left:0;top:568px;width:1200px;height:331px;background:linear-gradient(180deg,var(--red) 0%,#b0111a 100%)}
.welcome-title{left:120px;top:62px;font-family:"Oswald",sans-serif;font-weight:400;font-size:46px;line-height:46px;letter-spacing:2px;color:transparent;-webkit-text-stroke:1.5px var(--yellow)}
.season{left:120px;top:174px;width:307px;text-align:center;font-family:"Roboto Condensed",sans-serif;font-size:19px;color:var(--white);letter-spacing:1px}
.btn-register{left:125px;top:208px;width:302px;height:56px;border-radius:28px;background:linear-gradient(180deg,#ffd84a,var(--yellow-dark));border:2px solid #fff2a8;display:flex;align-items:center}
.btn-register .ball{width:40px;height:40px;margin-left:10px;border-radius:50%;background:#2b2b2b;border:3px solid #ffe780}
.btn-register b{margin-left:26px;font-family:"Roboto Condensed",sans-serif;font-size:24px;letter-spacing:1px;color:#2d2410}
.talk-title{left:480px;top:66px;font-family:"Oswald",sans-serif;font-size:27px;letter-spacing:1.5px;color:transparent;-webkit-text-stroke:1px #f6b8bb}
.talk-lead{left:480px;top:126px;width:610px;font-size:16px;line-height:24px;color:var(--white)}
.talk-body{left:480px;top:195px;width:610px;font-size:13px;line-height:21px;color:#f4d6d7}

/* fixtures */
.fixtures{left:0;top:899px;width:1200px;height:645px;background:linear-gradient(180deg,#e7eaee 0%,#dfe3e8 45%,#f6f7f8 100%)}
.fixtures-title{left:0;top:80px;width:1200px;text-align:center;font-family:"Oswald",sans-serif;font-size:34px;letter-spacing:2px;color:transparent;-webkit-text-stroke:1px var(--red)}
.fixtures-intro{left:144px;top:134px;width:912px;text-align:center;font-size:15px;line-height:23px;color:#444}
.fixtures-rule{left:145px;top:205px;width:925px;height:1px;background:#c9cdd2}
.col-rule{top:245px;width:1px;height:360px;background:#b9bec4}
.league{list-style:none;top:260px;font-family:"Roboto Condensed",sans-serif;font-weight:700;font-size:18px;color:#1d1d1d}
.league li{height:33.6px;display:flex;align-items:center}
.league li::before{content:"";width:12px;height:12px;border-radius:50%;background:#333;border:2px solid #bbb;margin-right:19px}

/* no smoking */
.smoking{left:0;top:1544px;width:1200px;height:245px;background:linear-gradient(90deg,#e9e9ea 0%,#f4f4f4 60%,#ebebeb 100%)}
.smoking-photo{left:528px;top:0;width:592px;height:245px;background:radial-gradient(ellipse at 50% 58%,#ffffff 0%,#e6e6e6 45%,#d9d9d9 100%)}
.smoking-title{left:120px;top:62px;display:flex;align-items:center;font-family:"Oswald",sans-serif;font-weight:300;font-size:48px;letter-spacing:2px;line-height:1}
.smoking-title .no{color:#444;margin-left:16px}
.smoking-title .word{color:var(--red-bright);margin-left:14px}
.smoking-sub{left:120px;top:128px;font-size:20px;color:#444}
.btn-yellow{left:120px;top:158px;width:112px;height:28px;border-radius:14px;background:var(--yellow);border:2px solid #fff3b0;font-size:9px;line-height:24px;text-align:center;color:#333;box-shadow:0 0 0 1px var(--yellow-dark)}

/* sponsors */
.sponsors-tag{left:498px;top:1832px;width:206px;height:43px;background:var(--red);color:var(--white);font-family:"Roboto Condensed",sans-serif;font-size:21px;line-height:43px;text-align:center;clip-path:polygon(5% 0,95% 0,100% 50%,95% 100%,5% 100%,0 50%)}
.sponsor{top:1906px;height:73px;border:1px solid #ddd;background:var(--white);display:flex;align-items:center;justify-content:center;gap:6px;font-family:"Roboto Condensed",sans-serif;font-weight:700;font-size:15px;color:#444;text-align:center;line-height:1.1}
.sponsor i{width:14px;height:14px;background:#444;flex:none}
.car-btn{top:1906px;height:73px;width:28px}
.car-prev{left:115px;background:#e5e5e5}
.car-next{left:1066px;background:var(--red)}
.car-btn svg{position:absolute;left:50%;top:50%;transform:translate(-50%,-50%)}

/* footer */
.footer{left:0;top:2021px;width:1200px;height:379px;background:var(--footer)}
.f-title{top:66px;font-size:17px;color:var(--red-bright);text-transform:uppercase}
.f-rule{top:96px;height:1px;background:var(--footer-line)}
.sitemap{left:120px;top:110px;list-style:none;font-size:13px;color:#bbb}
.sitemap li{height:28px;display:flex;align-items:center}
.sitemap li::before{content:"";width:7px;height:7px;border:1.5px solid #999;margin-right:13px}
.sitemap li.current{color:var(--yellow)}
.sitemap li.current::before{border-color:var(--yellow)}
.news{left:394px;width:310px;height:46px;display:flex;gap:10px}
.news .thumb{width:64px;height:42px;background:linear-gradient(135deg,#777,#444);flex:none}
.news p{font-size:11.5px;line-height:14px;color:#ccc;font-weight:600}
.news small{display:block;font-size:9px;color:#888;font-style:italic;font-weight:400;margin-top:3px}
.news-arrows{left:676px;top:64px;display:flex;gap:6px}
.news-arrows span{width:16px;height:16px;border-radius:50%}
.view-all{left:1019px;top:61px;width:61px;height:16px;border-radius:8px;background:var(--yellow);font-size:8px;line-height:16px;text-align:center;color:#333}
.gallery{left:797px;top:113px;width:281px;height:183px;display:grid;grid-template-columns:repeat(3,1fr);grid-template-rows:repeat(3,1fr);gap:3px}
.gallery div{background:linear-gradient(135deg,#8a6a5a,#5a3d35)}
.gallery .tall{grid-row:span 2;background:linear-gradient(160deg,#c42a2a,#5d4a40)}
.f-bottom{left:120px;top:325px;width:960px;height:1px;background:var(--footer-line)}
.copyright{left:120px;top:346px;font-size:11px;color:#888}
.social{left:916px;top:338px;display:flex;gap:10px}
.social span{width:26px;height:26px;border-radius:50%;border:1.5px solid #777}
.social span:first-child{border-color:#3fa3de}
</style>
</head>
<body>

<!-- hero -->
<section class="hero abs" role="img" aria-label="Blurred stadium crowd behind a running footballer in a red kit">
  <div class="hero-player abs" role="img" aria-label="Footballer in red kit sprinting with the ball"></div>
  <div class="hero-mark abs"><span></span>Tavenhurst FC</div>
  <h1 class="hero-title abs">TAVENHURST FC</h1>
  <p class="hero-text abs">Lorem Ipsum is simply dummy text of the printing and typesetting industry. Lorem Ipsum has been the industry's standard dummy text .</p>
  <a class="btn-red abs">FIND OUT MORE</a>
  <div class="arrow-left abs"><svg width="24" height="24" viewBox="0 0 24 24" style="left:20px"><circle cx="12" cy="12" r="11" fill="#fff"/><path d="M14 7l-5 5 5 5" stroke="#111" stroke-width="3" fill="none"/></svg></div>
  <div class="arrow-right abs"><svg width="26" height="26" viewBox="0 0 24 24" style="left:8px"><circle cx="12" cy="12" r="11" fill="#111"/><path d="M10 7l5 5-5 5" stroke="#fff" stroke-width="3" fill="none"/></svg></div>
</section>

<!-- header -->
<header class="header abs">
  <svg width="1200" height="131" viewBox="0 0 1200 131"><polygon points="0,0 1200,0 1200,77 0,131" fill="#fff"/></svg>
  <div class="brand abs"><span class="brand-dot"></span>Tavenhurst FC</div>
  <ul class="nav abs">
    <li class="active">HOME</li><li>ABOUT US</li><li>NEWS</li><li>FIXTURE &amp; RESULTS</li><li>PHOTO GALLERY</li><li>SPONSOR</li><li>CLUB</li><li>CONTACT US</li>
  </ul>
</header>

<!-- welcome -->
<section class="welcome abs">
  <h2 class="welcome-title abs">WELCOME TO<br>TAVENHURST FC</h2>
  <p class="season abs">2014 SEASON</p>
  <a class="btn-register abs"><span class="ball"></span><b>REGISTER ONLINE</b></a>
  <h2 class="talk-title abs">LET'S TALK ABOUT TAVENHURST FC.</h2>
  <p class="talk-lead abs">Lorem Ipsum is simply dummy text of the printing and typesetting industry. Lorem Ipsum has been the industry's standard</p>
  <p class="talk-body abs">Dummy text ever since the 1500s, when an unknown printer took a galley of type and scrambled it to make a type specimen book. It has survived not only five centuries, but also the leap into electronic typesetting, remaining essentially unchanged.</p>
</section>

<!-- fixtures -->
<section class="fixtures abs" role="img" aria-label="Faded stadium pitch under floodlights">
  <h2 class="fixtures-title abs">FIXTURES &amp; RESULTS</h2>
  <p class="fixtures-intro abs">Lorem Ipsum is simply dummy text of the printing and typesetting industry. Lorem Ipsum has been the industry's standard dummy text ever since the 1500s, when an unknown printer took a galley of type and scrambled it to make a type specimen book.</p>
  <div class="fixtures-rule abs"></div>
  <div class="col-rule abs" style="left:435px"></div>
  <div class="col-rule abs" style="left:771px"></div>
  <ul class="league abs" style="left:145px">
    <li>PREMIER LEAGUE</li><li>PREMIER LEAGUE RES</li><li>SUPER LEAGUE</li><li>SUPER LEAGUE RES</li><li>UNDER 16 / 2</li><li>UNDER 17 / 1</li><li>UNDER 10 / 2</li><li>UNDER 10 / 3</li><li>UNDER 11 / 1</li><li>UNDER 12 / 3</li>
  </ul>
  <ul class="league abs" style="left:539px">
    <li>UNDER 13 / 3</li><li>UNDER 14 / 3</li><li>AA MEN / 5</li><li>AA MEN / 6</li><li>AA MEN / 8</li><li>AA MEN / 10</li><li>AA MEN / 10</li><li>AA MEN / 14</li><li>07 ECL / RED</li><li>07 ECL / GREEN</li>
  </ul>
  <ul class="league abs" style="left:875px">
    <li>07 ECL / BLUE</li><li>08 ECL / BLUE</li><li>08 ECL / GREEN</li><li>09 / GREEN</li><li>06 / A GREEN</li><li>06 / B BLUE</li><li>06 / C RED</li><li>06 / D PURPLE</li><li>06 / E WHITE</li><li>06 / F BROWN</li>
  </ul>
</section>

<!-- no smoking -->
<section class="smoking abs">
  <div class="smoking-photo abs" role="img" aria-label="White ashtray surrounded by scattered cigarette butts and ash"></div>
  <h2 class="smoking-title abs">
    <svg width="38" height="38" viewBox="0 0 38 38"><circle cx="19" cy="19" r="16" fill="none" stroke="#e3242b" stroke-width="3"/><line x1="8" y1="8" x2="30" y2="30" stroke="#e3242b" stroke-width="3"/><rect x="10" y="20" width="18" height="4" fill="#e3242b"/></svg>
    <span class="no">NO</span><span class="word">SMOKING</span>
  </h2>
  <p class="smoking-sub abs">There is a No Smoking Ban for all Sports Grounds</p>
  <a class="btn-yellow abs">FIND OUT MORE</a>
</section>

<!-- sponsors -->
<section class="sponsors">
  <h2 class="sponsors-tag abs">OUR SPONSORS</h2>
  <div class="car-btn car-prev abs"><svg width="12" height="20" viewBox="0 0 12 20"><path d="M10 2L2 10l8 8" stroke="#fff" stroke-width="2.5" fill="none"/></svg></div>
  <div class="sponsor abs" style="left:149px;width:166px"><i></i>Brightside Media</div>
  <div class="sponsor abs" style="left:325px;width:131px">Kestrel</div>
  <div class="sponsor abs" style="left:466px;width:144px">Vantor</div>
  <div class="sponsor abs" style="left:619px;width:170px">Halden Perry &amp; Co</div>
  <div class="sponsor abs" style="left:798px;width:148px">Surecoat</div>
  <div class="sponsor abs" style="left:955px;width:104px;font-size:12px">Tavenhurst<br>Bowling Club</div>
  <div class="car-btn car-next abs"><svg width="12" height="20" viewBox="0 0 12 20"><path d="M2 2l8 8-8 8" stroke="#fff" stroke-width="2.5" fill="none"/></svg></div>
</section>

<!-- footer -->
<footer class="footer abs">
  <h3 class="f-title abs" style="left:120px">Site Map</h3>
  <div class="f-rule abs" style="left:120px;width:200px"></div>
  <ul class="sitemap abs">
    <li>Become A Referee</li><li>News</li><li>Fixture &amp; Results</li><li class="current">Photo Gallery</li><li>Sponsor</li><li>Club</li><li>Contact Us</li>
  </ul>

  <h3 class="f-title abs" style="left:392px">Latest News</h3>
  <div class="news-arrows abs"><span style="background:#666"></span><span style="background:var(--yellow)"></span></div>
  <div class="f-rule abs" style="left:392px;width:320px"></div>
  <div class="news abs" style="top:118px"><div class="thumb" role="img" aria-label="Match photo"></div><p>Lorem Ipsum is simply dummy text of the typesetting industry.<small>Mar 11, 2014</small></p></div>
  <div class="news abs" style="top:182px"><div class="thumb" role="img" aria-label="Match photo"></div><p>Lorem Ipsum is simply dummy text of the typesetting industry.<small>Mar 11, 2014</small></p></div>
  <div class="news abs" style="top:246px"><div class="thumb" role="img" aria-label="Match photo"></div><p>Lorem Ipsum is simply dummy text of the typesetting industry.<small>Mar 11, 2014</small></p></div>

  <h3 class="f-title abs" style="left:795px">Photo Gallery</h3>
  <span class="view-all abs">VIEW ALL</span>
  <div class="f-rule abs" style="left:795px;width:285px"></div>
  <div class="gallery abs">
    <div class="tall" role="img" aria-label="Young player holding a trophy"></div>
    <div role="img" aria-label="Club members group photo"></div>
    <div role="img" aria-label="Club members group photo"></div>
    <div role="img" aria-label="Player in red kit"></div>
    <div role="img" aria-label="Team on the pitch"></div>
    <div role="img" aria-label="Players lined up"></div>
    <div role="img" aria-label="Players celebrating"></div>
    <div role="img" aria-label="Junior team photo"></div>
  </div>

  <div class="f-bottom abs"></div>
  <p class="copyright abs">Copyright TAVENHURST FC &reg; 2014. All rights reserved. Terms and Conditions</p>
  <div class="social abs"><span></span><span></span><span></span><span></span><span></span></div>
</footer>

</body>
</html>
```